Request for Business Card Design

Hi. My name is Marlene, I am looking for a new business card design for my company, Quarrow Signal Instruments, LLC. I really like the design you did for Tarsel Venture and was hoping you could do something similar using our full logo and our mark. I am also open to any raised texture design using our mark. I have attached our full logo, which would need to be somewhere on the card, as well as the mark in both outline and full form, as well as our brand colors / guide. The card does not have to be white, as long as our logo and mark appear. I actually like darker colored business cards more, but am open to all options. If you are interested in working with me, please let me know. We would also take the business card design into letterhead design if you can do that.

```html
<!DOCTYPE html>
<html lang="en">
<head>
<meta charset="utf-8">
<title>Quarrow Signal Instruments – Business Card</title>
<link rel="stylesheet" href="https://fonts.googleapis.com/css2?family=Open+Sans:wght@400;600;700&display=swap">
<style>
  :root {
    --stage: #232323;
    --card: #3d3d3f;
    --card-deep: #2f2f31;
    --brand-blue: #1a9cc8;
    --white: #ffffff;
    --text: #f2f2f2;
  }
  html, body {
    margin: 0;
    width: 1200px;
    height: 780px;
    overflow: hidden;
    background: var(--stage);
    font-family: "Open Sans", Arial, sans-serif;
  }
  .canvas {
    position: relative;
    width: 1200px;
    height: 780px;
  }
  .card {
    position: absolute;
    width: 600px;
    height: 340px;
    border-radius: 22px;
    background: var(--card);
    box-shadow: 0 0 0 4px var(--brand-blue), 0 18px 40px rgba(0,0,0,.55);
    overflow: hidden;
  }
  .card--back { left: 60px; top: 50px; }
  .card--front { left: 540px; top: 400px; }

  /* back */
  .back-texture {
    position: absolute;
    inset: 0;
    background: linear-gradient(200deg, #6a6a6c 0%, #4a4a4c 30%, #363638 60%, #2e2e30 100%);
  }
  .back-brand {
    position: absolute;
    right: 28px;
    bottom: 30px;
    display: flex;
    align-items: center;
    gap: 8px;
    color: var(--white);
    font-weight: 700;
    font-size: 14px;
    letter-spacing: .04em;
    text-transform: uppercase;
  }
  .brand-dot {
    width: 14px;
    height: 14px;
    border-radius: 50%;
    background: var(--brand-blue);
  }

  /* front */
  .front-bands { position: absolute; inset: 0; }
  .front-brand {
    position: absolute;
    left: 30px;
    top: 34px;
    display: flex;
    align-items: center;
    gap: 12px;
    color: var(--white);
    font-weight: 700;
    font-size: 22px;
    letter-spacing: .05em;
    text-transform: uppercase;
  }
  .front-brand .brand-dot { width: 30px; height: 30px; }

  .person {
    position: absolute;
    right: 40px;
    top: 150px;
    text-align: right;
  }
  .person-name {
    margin: 0;
    color: var(--brand-blue);
    font-weight: 600;
    font-size: 38px;
    line-height: 1;
  }
  .person-role {
    margin: 4px 0 0;
    color: var(--white);
    font-size: 15px;
  }

  .address {
    position: absolute;
    left: 34px;
    top: 120px;
    margin: 0;
    color: var(--text);
    font-style: normal;
    font-size: 15px;
    line-height: 1.4;
  }
  .contacts {
    position: absolute;
    left: 34px;
    top: 178px;
    margin: 0;
    padding: 0;
    list-style: none;
    color: var(--text);
    font-size: 14px;
    line-height: 22px;
  }
  .contacts li { display: flex; align-items: center; gap: 10px; }
  .contacts svg { width: 14px; height: 14px; fill: var(--brand-blue); }
</style>
</head>
<body>
<main class="canvas">

  <section class="card card--back" aria-label="Business card, back">
    <div class="back-texture" role="img" aria-label="Repeating raised texture of the company mark"></div>
    <div class="back-brand"><span class="brand-dot"></span>Quarrow Signal Instruments</div>
  </section>

  <section class="card card--front" aria-label="Business card, front">
    <svg class="front-bands" viewBox="0 0 600 340" preserveAspectRatio="none" aria-hidden="true">
      <polygon points="340,262 600,236 600,262 372,290" fill="var(--white)"/>
      <polygon points="0,312 0,340 600,340 600,262 372,290 340,290" fill="var(--brand-blue)"/>
    </svg>

    <div class="front-brand"><span class="brand-dot"></span>Quarrow Signal Instruments</div>

    <div class="person">
      <p class="person-name">Marlene</p>
      <p class="person-role">Director</p>
    </div>

    <address class="address">1180 Harlow Park Drive •<br>Brinfield, CO 80611</address>

    <ul class="contacts">
      <li>
        <svg viewBox="0 0 24 24" aria-hidden="true"><path d="M6.6 10.8a15 15 0 0 0 6.6 6.6l2.2-2.2a1 1 0 0 1 1-.25 11.4 11.4 0 0 0 3.6.6 1 1 0 0 1 1 1V20a1 1 0 0 1-1 1A17 17 0 0 1 3 4a1 1 0 0 1 1-1h3.5a1 1 0 0 1 1 1c0 1.25.2 2.45.6 3.6a1 1 0 0 1-.25 1z"/></svg>
        +001 555 210 4830
      </li>
      <li>
        <svg viewBox="0 0 24 24" aria-hidden="true"><path d="M6 2h10v6H6zM3 9h18v11H3zm3 3v2h2v-2zm4 0v2h2v-2zm4 0v2h4v-2zM6 16v2h2v-2zm4 0v2h2v-2z"/></svg>
        +001 555 210 4831
      </li>
      <li>
        <svg viewBox="0 0 24 24" aria-hidden="true"><path d="M12 2a10 10 0 1 0 0 20 10 10 0 0 0 0-20zm6.9 6h-3a15 15 0 0 0-1.3-3.9A8 8 0 0 1 18.9 8zM12 4c.8 1.2 1.5 2.5 1.9 4h-3.8c.4-1.5 1.1-2.8 1.9-4zM4.3 14a8 8 0 0 1 0-4h3.4a16 16 0 0 0 0 4zm.8 2h3a15 15 0 0 0 1.3 3.9A8 8 0 0 1 5.1 16zm3-8h-3a8 8 0 0 1 4.3-3.9A15 15 0 0 0 8.1 8zM12 20c-.8-1.2-1.5-2.5-1.9-4h3.8c-.4 1.5-1.1 2.8-1.9 4zm2.3-6H9.7a14 14 0 0 1 0-4h4.6a14 14 0 0 1 0 4zm.3 5.9a15 15 0 0 0 1.3-3.9h3a8 8 0 0 1-4.3 3.9zm1.7-5.9a16 16 0 0 0 0-4h3.4a8 8 0 0 1 0 4z"/></svg>
        www.quarrowsignal.com
      </li>
      <li>
        <svg viewBox="0 0 24 24" aria-hidden="true"><path d="M2 5h20v14H2zm2 2v.5l8 5 8-5V7zm0 2.8V17h16V9.8l-8 5z"/></svg>
        info@quarrowsignal.com
      </li>
    </ul>
  </section>

</main>
</body>
</html>
```